Moravel Aesthetic Doctor

I require an elegant, luxurious looking business card for my aesthetic business. I am a doctor and that will set me aside from competitors. I am planning to provide home and spa based treatments to clients with high expectations. I have attached my logo.

```html
<!DOCTYPE html>
<html lang="en">
<head>
<meta charset="utf-8">
<title>Moravel Aesthetic Doctor – Business Card</title>
<link href="https://fonts.googleapis.com/css2?family=Montserrat:wght@500&family=Roboto:wght@300;400&display=swap" rel="stylesheet">
<style>
  :root {
    --backdrop: #c8c9cb;
    --card-top: #ffffff;
    --card-bottom: #eceded;
    --ink: #2b2d31;
    --brand-grey: #8a909e;
    --brand-blue: #3a9ad6;
    --band-dark: #1c6fb4;
    --band-light: #4b9fd8;
    --wave-blue: #4ba2d6;
    --wave-grey: #8c93a2;
    --wave-grey-soft: #b4b9c4;
    --white: #ffffff;
  }
  * { box-sizing: border-box; margin: 0; padding: 0; }
  html, body { width: 1200px; height: 576px; overflow: hidden; }
  body {
    background: var(--backdrop);
    font-family: "Roboto", Arial, sans-serif;
    position: relative;
  }
  .card {
    position: absolute;
    width: 484px;
    height: 293px;
    border-radius: 10px;
    overflow: hidden;
    background: linear-gradient(180deg, var(--card-top), var(--card-bottom));
  }
  .card--front { left: 82px; top: 139px; }
  .card--back  { left: 602px; top: 138px; width: 481px; height: 292px; }

  /* brand lockup: one colour, one weight */
  .brand { position: absolute; color: var(--brand-grey); font-weight: 300; line-height: 1; }
  .brand__mark {
    position: absolute;
    border: 2px solid var(--brand-grey);
    border-radius: 50%;
  }
  .brand__name { position: absolute; white-space: nowrap; letter-spacing: 1px; }
  .brand__tag  { position: absolute; white-space: nowrap; letter-spacing: 1.5px; }

  .card--front .brand__mark { left: 100px; top: 61px; width: 86px; height: 86px; }
  .card--front .brand__name { left: 200px; top: 64px; font-size: 50px; }
  .card--front .brand__tag  { left: 201px; top: 119px; font-size: 21px; }

  .card--back .brand__mark { left: 24px; top: 28px; width: 84px; height: 84px; }
  .card--back .brand__name { left: 131px; top: 34px; font-size: 48px; }
  .card--back .brand__tag  { left: 132px; top: 86px; font-size: 20px; }

  .services {
    position: absolute; left: 0; right: 0; top: 194px;
    text-align: center; font-size: 13.5px; color: var(--ink); line-height: 19px;
  }
  .services__sep { color: var(--brand-blue); margin: 0 7px; }

  .band {
    position: absolute; left: 0; right: 0; top: 239px; height: 34px;
    background: linear-gradient(90deg, var(--band-dark), var(--band-light) 60%, var(--band-dark));
    color: var(--white);
    font-family: "Montserrat", Arial, sans-serif; font-weight: 500;
    font-size: 12.5px; letter-spacing: 1px;
    display: flex; align-items: center; justify-content: center;
  }

  .waves { position: absolute; left: 0; top: 0; }

  .person { position: absolute; left: 26px; top: 156px; }
  .person__name { font-size: 20px; color: var(--ink); font-weight: 400; }
  .person__post { font-size: 10px; color: var(--brand-blue); margin-left: 6px; vertical-align: 3px; }
  .person__qual {
    margin-top: 8px; font-size: 13px; line-height: 16px; color: var(--brand-blue);
  }

  .contact {
    position: absolute; right: 20px; top: 196px;
    list-style: none; text-align: right; color: var(--white); font-size: 13px;
  }
  .contact__item { display: flex; justify-content: flex-end; align-items: center; height: 19px; }
  .contact__item--social { margin-bottom: 6px; }
  .contact__icon { width: 11px; height: 11px; margin-left: 8px; flex: none; }
  .contact__dot {
    width: 11px; height: 11px; border-radius: 50%; background: var(--white);
    margin-left: 4px; flex: none;
  }
  .contact__dot:first-of-type { margin-left: 6px; }
</style>
</head>
<body>

  <section class="card card--front" aria-label="Card front">
    <div class="brand">
      <span class="brand__mark"></span>
      <span class="brand__name">MORAVEL</span>
      <span class="brand__tag">AESTHETIC DOCTOR</span>
    </div>
    <p class="services">
      Dermal Injectables<span class="services__sep">|</span>Plasma Facials<span class="services__sep">|</span>Microneedling<br>
      Skin Boosters<span class="services__sep">|</span>Excessive Sweating
    </p>
    <div class="band">HOME AND SPA BASED TREATMENTS</div>
  </section>

  <section class="card card--back" aria-label="Card back">
    <svg class="waves" width="481" height="292" viewBox="0 0 481 292" aria-hidden="true">
      <path d="M0,232 C90,268 190,262 270,232 C350,202 410,170 481,166 L481,292 L0,292 Z" fill="var(--wave-blue)"/>
      <path d="M0,216 C90,252 190,250 270,220 C350,190 410,160 481,152" fill="none" stroke="var(--wave-grey)" stroke-width="7"/>
      <path d="M40,252 C130,262 215,252 290,226" fill="none" stroke="var(--wave-grey-soft)" stroke-width="3"/>
    </svg>

    <div class="brand">
      <span class="brand__mark"></span>
      <span class="brand__name">MORAVEL</span>
      <span class="brand__tag">AESTHETIC DOCTOR</span>
    </div>

    <div class="person">
      <p><span class="person__name">Dr Elin Varga</span><span class="person__post">MRCPCH MD</span></p>
      <p class="person__qual">Australasian Diploma of<br>Aesthetic Medicine</p>
    </div>

    <ul class="contact">
      <li class="contact__item contact__item--social">Follows:<span class="contact__dot"></span><span class="contact__dot"></span></li>
      <li class="contact__item">0800 555 014
        <svg class="contact__icon" viewBox="0 0 12 12" aria-hidden="true"><path d="M2.5 1 L4.5 1 L5.3 3.4 L4 4.4 C4.7 5.9 6.1 7.3 7.6 8 L8.6 6.7 L11 7.5 L11 9.5 C11 10.3 10.3 11 9.5 11 C5 11 1 7 1 2.5 C1 1.7 1.7 1 2.5 1 Z" fill="var(--white)"/></svg>
      </li>
      <li class="contact__item">www.moravel.co.nz
        <svg class="contact__icon" viewBox="0 0 12 12" aria-hidden="true"><rect x="0.5" y="2.5" width="11" height="7.5" rx="1" fill="var(--white)"/><path d="M1 3 L6 7 L11 3" fill="none" stroke="var(--wave-blue)" stroke-width="1"/></svg>
      </li>
      <li class="contact__item">elin@moravel.co.nz
        <svg class="contact__icon" viewBox="0 0 12 12" aria-hidden="true"><g fill="none" stroke="var(--white)" stroke-width="1"><circle cx="6" cy="6" r="5"/><ellipse cx="6" cy="6" rx="2.2" ry="5"/><path d="M1 6 H11 M2 3.5 H10 M2 8.5 H10"/></g></svg>
      </li>
    </ul>
  </section>

</body>
</html>
```